Virtual Racing Community for Runners Needs a Refreshed Web Design

We are a STARTUP. The current website consists of 3 main pages that function well; however, they are not producing the proper conversions because we need a more professional look and better execution of our great ideas.

First page: landing page that needs to be intriguing, sleek, create urgency, incorporate our call to action and most importantly get the consumer to click a button to get to second page. www.lomberun.com

Second page: sign up page that incorporates our already existing postwren form that doesn't take the viewer away from the page on incorrect form field entry. On successful completion needs to inform the viewer to check the email and confirm (possibly in spam) and open third page. http://www.lomberun.com/beta.html

Third page: preorder page that allows the user prepurchase through a well working form through "www.getparsnip.com." This interface works really well; however, the graphics and page need to really entice the viewer to buy. http://www.lomberun.com/preorder.html

And that's it!!! Simple 3 pages that function currently 95% how we want it, but really needs that creative touch to push it to the next level!

Contact us with any other questions!
Updates

Project Deadline Extended
Reason: I have provided numerous feedback and am awaiting redesigns. Have it narrowed down to 2 designers. Need time to vet with stakeholders.

Industry/Entity Type

Racing

```html
<!DOCTYPE html>
<html lang="en">
<head>
<meta charset="utf-8">
<title>Lomberun — Keep Your Social Life While You Race</title>
<link href="https://fonts.googleapis.com/css2?family=Bebas+Neue&family=Arimo:wght@400;700&display=swap" rel="stylesheet">
<style>
  :root {
    --ink: #1e2e35;
    --black: #111111;
    --slate: #475b63;
    --slate-text: #b9cad0;
    --tan: #c4a98b;
    --sky: #a8c4ce;
    --body: #444444;
    --footer: #141414;
    --footer-text: #dddddd;
    --white: #ffffff;
  }
  * { box-sizing: border-box; margin: 0; padding: 0; }
  html, body { width: 1200px; height: 1053px; overflow: hidden; background: var(--white); }
  body { position: relative; font-family: "Arimo", Arial, sans-serif; color: var(--body); }
  .display { font-family: "Bebas Neue", "Oswald", sans-serif; font-weight: 400; }

  .hero {
    position: absolute; left: 0; top: 0; width: 1200px; height: 522px;
    background: linear-gradient(100deg, #5b6063 0%, #8a8d8c 18%, #c8c9c5 38%, #e7e6e1 55%, #d9dbd8 75%, #9aa3a4 100%);
  }
  .hero-copy { position: absolute; left: 605px; top: 0; width: 560px; }
  .brand { position: absolute; top: 22px; left: 2px; font-size: 104px; letter-spacing: 6px; color: var(--black); line-height: 1; }
  .headline { position: absolute; top: 138px; left: 0; font-size: 60px; line-height: 57px; color: var(--ink); white-space: nowrap; }
  .tagline { position: absolute; top: 252px; left: 0; font-size: 46px; line-height: 1; color: var(--ink); letter-spacing: 1px; white-space: nowrap; opacity: .92; }
  .promo-title { position: absolute; top: 318px; left: 0; font-size: 42px; line-height: 1; color: var(--black); white-space: nowrap; }
  .promo-text { position: absolute; top: 365px; left: 3px; width: 360px; font-size: 14.5px; line-height: 17px; color: var(--black); }
  .register { position: absolute; top: 415px; left: 0; width: 254px; height: 54px; display: flex; text-decoration: none; }
  .register-arrow { width: 60px; background: var(--black); display: flex; align-items: center; justify-content: center; }
  .register-label { flex: 1; background: var(--slate); color: var(--sky); font-size: 38px; display: flex; align-items: center; justify-content: center; padding-top: 4px; }

  .news-card { position: absolute; left: 110px; top: 486px; width: 980px; height: 314px; background: var(--white); box-shadow: 0 10px 24px rgba(0,0,0,.12); }
  .news-banner { height: 104px; background: var(--slate); display: flex; }
  .news-date { width: 98px; background: var(--tan); color: var(--white); display: flex; flex-direction: column; align-items: center; padding-top: 18px; }
  .news-day { width: 44px; height: 44px; border: 2px solid var(--white); border-radius: 50%; display: flex; align-items: center; justify-content: center; font-size: 21px; }
  .news-month { margin-top: 8px; font-size: 14px; letter-spacing: .5px; }
  .news-body { padding: 15px 16px 0; flex: 1; }
  .news-title { font-size: 17px; color: var(--white); font-weight: 400; margin-bottom: 12px; }
  .news-text { font-size: 13px; line-height: 16px; color: var(--slate-text); }

  .feature { position: absolute; top: 176px; display: flex; }
  .feature-icon { width: 50px; height: 50px; margin-right: 8px; }
  .feature h3 { font-size: 18px; font-weight: 400; color: #222; margin-bottom: 6px; }
  .feature p { font-size: 12.5px; line-height: 15.5px; color: var(--body); width: 232px; height: 52px; }
  .view-btn { display: flex; width: 77px; height: 25px; margin-top: 5px; text-decoration: none; }
  .view-btn span:first-child { width: 48px; background: var(--slate); color: var(--white); font-size: 12px; padding: 5px 0 0 11px; }
  .view-btn span:last-child { flex: 1; background: var(--black); display: flex; align-items: center; justify-content: center; }

  .footer { position: absolute; left: 0; top: 862px; width: 1200px; height: 191px; background: var(--footer); }
  .connect-title { position: absolute; left: 113px; top: 30px; font-size: 29px; color: var(--white); letter-spacing: .5px; }
  .social { position: absolute; left: 115px; top: 71px; display: flex; gap: 20px; }
  .social span { width: 40px; height: 40px; border: 2px solid var(--white); border-radius: 50%; }
  .contact { position: absolute; left: 829px; color: var(--footer-text); display: flex; align-items: center; }
  .contact-icon { width: 32px; height: 32px; border: 2px solid var(--white); border-radius: 50%; display: flex; align-items: center; justify-content: center; margin-right: 12px; }
  .contact-address { top: 32px; font-size: 12px; line-height: 18px; }
  .contact-phone { top: 74px; font-size: 24px; color: #c8c8c8; }
  .legal { position: absolute; left: 0; top: 128px; width: 1200px; height: 47px; background: var(--tan); color: var(--white); font-size: 11px; }
  .legal-copy { position: absolute; left: 115px; top: 18px; }
  .legal-links { position: absolute; right: 115px; top: 18px; }
</style>
</head>
<body>
  <section class="hero" role="img" aria-label="Photo of a man and woman running on treadmills in a bright gym"></section>

  <div class="hero-copy">
    <div class="brand display">LOMBERUN</div>
    <h1 class="headline display">KEEP YOUR SOCIAL LIFE<br>WHILE YOU RACE</h1>
    <p class="tagline display">COMMUNICATE. CELEBRATE. CULTIVATE.</p>
    <h2 class="promo-title display">CHICAGO BETA RUN WEEK 2</h2>
    <p class="promo-text">For a limited time be the first to receive early access and receive a Real Life Beta Tester t-shirt.</p>
    <a class="register" href="#">
      <span class="register-arrow">
        <svg width="26" height="20" viewBox="0 0 26 20"><path d="M2 10h20M14 2l8 8-8 8" fill="none" stroke="#a8c4ce" stroke-width="3"/></svg>
      </span>
      <span class="register-label display">REGISTER NOW</span>
    </a>
  </div>

  <section class="news-card">
    <div class="news-banner">
      <div class="news-date"><span class="news-day">23</span><span class="news-month">AUG</span></div>
      <div class="news-body">
        <h2 class="news-title">Latest Virtual Run</h2>
        <p class="news-text">Lorem ipsum dolor sit amet, consectetur adipisicing elit, sed do eiusmod tempor incididunt ut labore et dolore magna aliqua. Ut enim ad minim veniam, quis nostrud exercitation ullamco laboris nisi ut aliquip ex ea commodo consequat.</p>
      </div>
    </div>

    <div class="feature" style="left:25px">
      <svg class="feature-icon" viewBox="0 0 50 50"><path d="M12 2h26v12c0 8-6 13-13 13S12 22 12 14z M12 5H3v6c0 6 5 9 10 9 M38 5h9v6c0 6-5 9-10 9" fill="#333" stroke="#333" stroke-width="2"/><rect x="21" y="26" width="8" height="8" fill="#333"/><rect x="14" y="34" width="22" height="8" fill="#333"/></svg>
      <div>
        <h3>freebies and giveaways</h3>
        <p>Duis aute irure dolor in reprehenderit in voluptate velit esse cillum dolore eu fugiat nulla pariatur.</p>
        <a class="view-btn" href="#"><span>view</span><span><svg width="12" height="10" viewBox="0 0 12 10"><path d="M1 5h9M6 1l4 4-4 4" fill="none" stroke="#fff" stroke-width="1.6"/></svg></span></a>
      </div>
    </div>

    <div class="feature" style="left:345px">
      <svg class="feature-icon" viewBox="0 0 50 50"><path d="M2 28h30M8 20h22M14 12h18" stroke="#333" stroke-width="3"/><path d="M24 46v-14" stroke="#333" stroke-width="2"/><circle cx="40" cy="14" r="7" fill="none" stroke="#333" stroke-width="3"/></svg>
      <div>
        <h3>run at your own pace</h3>
        <p>You can walk, jog, skip or run the distance of your choice. You can complete your race at the gym ...</p>
        <a class="view-btn" href="#"><span>view</span><span><svg width="12" height="10" viewBox="0 0 12 10"><path d="M1 5h9M6 1l4 4-4 4" fill="none" stroke="#fff" stroke-width="1.6"/></svg></span></a>
      </div>
    </div>

    <div class="feature" style="left:667px">
      <svg class="feature-icon" viewBox="0 0 50 50"><circle cx="19" cy="8" r="6" fill="none" stroke="#333" stroke-width="3"/><circle cx="37" cy="20" r="10" fill="#333"/><circle cx="16" cy="31" r="14" fill="#fff" stroke="#333" stroke-width="3"/><text x="16" y="37" font-size="17" font-family="Arimo, sans-serif" font-weight="700" fill="#333" text-anchor="middle">$</text><text x="37" y="25" font-size="13" font-family="Arimo, sans-serif" font-weight="700" fill="#fff" text-anchor="middle">$</text></svg>
      <div>
        <h3>discounts</h3>
        <p>If you have 10 or more runners interested in participating in one of our races, please contact us and ...</p>
        <a class="view-btn" href="#"><span>view</span><span><svg width="12" height="10" viewBox="0 0 12 10"><path d="M1 5h9M6 1l4 4-4 4" fill="none" stroke="#fff" stroke-width="1.6"/></svg></span></a>
      </div>
    </div>
  </section>

  <footer class="footer">
    <h2 class="connect-title display">CONNECT WITH US</h2>
    <div class="social" aria-label="Social links">
      <span></span><span></span><span></span><span></span>
    </div>
    <div class="contact contact-address">
      <span class="contact-icon"><svg width="16" height="16" viewBox="0 0 16 16"><path d="M1 8L8 2l7 6M3 7v7h4v-4h2v4h4V7" fill="#fff"/></svg></span>
      <span>48 Harbor Lane Studio 7<br>Westfield, New York 556090</span>
    </div>
    <div class="contact contact-phone">
      <span class="contact-icon"><svg width="16" height="16" viewBox="0 0 16 16"><path d="M4 1l3 3-2 2c1 2 3 4 5 5l2-2 3 3-2 3C7 15 1 9 1 3z" fill="#fff"/></svg></span>
      <span>012-555-0148</span>
    </div>
    <div class="legal">
      <span class="legal-copy">© Copyright 2014 Lomberun. All Rights Reserved</span>
      <span class="legal-links">Policy | Terms</span>
    </div>
  </footer>
</body>
</html>
```